CREATE A BUSINESS CARD FOR A BOAT CLEANING SERVICE

WE ARE STARTING A NEW BOAT CLEANING BUSINESS. WE DIVE UNDERWATER TO CLEAN BOAT HULLS, JETTIES, UNDERWATER STRUCTURES ETC. WE ARE LOOKING FOR AN UPPERMARKET MODERN LOGO AND BUSINESS CARD AS ALOT OF OUR TARGET MARKET WILL BE HIGH END. YOU HAVE TO DESIGN A BUSINESS CARD AND LOGO SEPERATELY .
THE BUSINESS CARD DIMESNION MUST BE STANDARD SIZE.
The standard dimensions of a printed business card are 3.5 x 2 inches

Target Market(s)

UNDERWATER SERVICED

Industry/Entity Type

Business

Contact Information for Business Card

HOLLAND UNDERWATER SERVICES

Font styles to use
Serif

Colors

Designer to choose colors to be used in the design.

Requirements
Must have
• HOLLAND
Nice to have
• dark
Should not have
• more than 3 colors

```html
<!DOCTYPE html>
<html lang="en">
<head>
<meta charset="utf-8">
<title>Holland Underwater Service – Business Card</title>
<link href="https://fonts.googleapis.com/css2?family=Lato:wght@400;700&display=swap" rel="stylesheet">
<style>
  :root {
    --backdrop: #1c1c1c;
    --brand-blue: #174f8a;
    --card-white: #ffffff;
    --ink: #2f2f2f;
    --muted: #6b6b6b;
  }
  * { margin: 0; padding: 0; box-sizing: border-box; }
  html, body {
    width: 1200px; height: 897px; overflow: hidden;
    background: var(--backdrop);
    font-family: "Lato", sans-serif;
  }
  .canvas { position: relative; width: 1200px; height: 897px; }
  .card {
    position: absolute; left: 303px; width: 595px; height: 338px;
    border-radius: 22px; overflow: hidden;
  }
  .card--front { top: 92px; background: var(--card-white); }
  .card--back { top: 469px; background: var(--brand-blue); color: var(--card-white); }
  .card > * { position: absolute; white-space: nowrap; }

  .brand-name {
    font-weight: 400; letter-spacing: 0.42em; line-height: 1;
  }
  .brand-tagline {
    font-weight: 400; letter-spacing: 0.24em; line-height: 1;
  }

  /* front */
  .front-brand { left: 0; width: 297px; text-align: center; }
  .card--front .brand-name { top: 180px; font-size: 27px; color: var(--brand-blue); padding-left: 0.42em; }
  .card--front .brand-tagline { top: 214px; font-size: 14px; color: var(--muted); padding-left: 0.24em; }
  .divider { left: 297px; top: 86px; width: 2px; height: 168px; background: var(--brand-blue); }
  .contact { left: 323px; color: var(--ink); }
  .contact-name { top: 84px; font-size: 21px; font-weight: 700; color: var(--brand-blue); letter-spacing: 0.02em; }
  .contact-role { top: 108px; font-size: 18px; }
  .contact-address { top: 136px; font-size: 14.5px; line-height: 19px; }
  .contact-list { top: 180px; list-style: none; font-size: 14.5px; line-height: 19px; }
  .contact-list li { display: flex; align-items: center; gap: 12px; }
  .contact-list svg { width: 14px; height: 14px; fill: var(--brand-blue); flex: none; }

  /* back */
  .back-brand { left: 0; width: 595px; text-align: center; }
  .card--back .brand-name { top: 184px; font-size: 34px; padding-left: 0.42em; }
  .card--back .brand-tagline { top: 230px; font-size: 19px; padding-left: 0.24em; }
  .back-web { top: 294px; left: 0; width: 595px; text-align: center; font-size: 17px; letter-spacing: 0.03em; }
</style>
</head>
<body>
<main class="canvas">
  <section class="card card--front" aria-label="Card front">
    <div class="front-brand brand-name">HOLLAND</div>
    <div class="front-brand brand-tagline">UNDERWATER SERVICE</div>
    <div class="divider"></div>
    <h1 class="contact contact-name">DAAN VERHOEF</h1>
    <p class="contact contact-role">CEO / Founder</p>
    <p class="contact contact-address">Havenkade 27 3011AB,<br>Rotterdam, The Netherlands</p>
    <ul class="contact contact-list">
      <li><svg viewBox="0 0 16 16"><path d="M3.6 1.2l2.3 2.9-1.3 1.8c.9 2 2.4 3.6 4.4 4.6l1.8-1.3 2.9 2.3-1.4 2.5C7.4 13.6 2.4 8.6 1.2 2.6z"/></svg>212-555-0147</li>
      <li><svg viewBox="0 0 16 16"><path d="M1 5c2-3 12-3 14 0v2h-3.5V5.5h-7V7H1zM4 8h8l2 6H2zm4 1.5a2 2 0 100 4 2 2 0 000-4z"/></svg>844-555-DIVE</li>
      <li><svg viewBox="0 0 16 16"><path d="M1 3h14v1.5L8 9 1 4.5zm0 3.2l7 4.4 7-4.4V13H1z"/></svg>info@hollandunderwater.com</li>
      <li><svg viewBox="0 0 16 16"><path d="M8 1a7 7 0 100 14A7 7 0 008 1zm0 1.3c.8.8 1.5 2.3 1.7 4H6.3C6.5 4.6 7.2 3.1 8 2.3zM2.4 7.3h2.6c0 .5 0 1 .1 1.4H2.4a5.7 5.7 0 010-1.4zm1-1h1.8c.1-1.2.5-2.4 1-3.3a5.7 5.7 0 00-2.8 3.3zm7.4 0h1.8A5.7 5.7 0 009.8 3c.5.9.9 2.1 1 3.3zm.2 1H13.6a5.7 5.7 0 010 1.4H11c.1-.4.1-.9 0-1.4zm-4.7 0h3.4a9 9 0 010 1.4H6.3a9 9 0 010-1.4zm-3 2.4h1.9c.1 1.2.5 2.4 1 3.3a5.7 5.7 0 01-2.9-3.3zm2.9 0h3.4c-.2 1.6-.9 3.1-1.7 3.9-.8-.8-1.5-2.3-1.7-3.9zm4.4 0h1.9a5.7 5.7 0 01-2.9 3.3c.5-.9.9-2.1 1-3.3z"/></svg>www.hollandunderwater.com</li>
    </ul>
  </section>

  <section class="card card--back" aria-label="Card back">
    <div class="back-brand brand-name">HOLLAND</div>
    <div class="back-brand brand-tagline">UNDERWATER SERVICE</div>
    <p class="back-web">www.hollandunderwater.com</p>
  </section>
</main>
</body>
</html>
```